Income Tax Flyer - Updates Needed

Just need to update this flyer design and give it a new look. We would like to keep all the same wording but make it stand out a little more. Our selling point is the "Same Day Tax Advance up to $6,000"

Lending, Small Loans, Tax Services, Title Loans, Personal Loans

```html
<!DOCTYPE html>
<html lang="en">
<head>
<meta charset="utf-8">
<title>Same Day Tax Advance Flyer</title>
<link href="https://fonts.googleapis.com/css2?family=Montserrat:wght@800;900&family=Poppins:wght@400;500;600;700;800&display=swap" rel="stylesheet">
<style>
:root{
  --red:#e31e24;
  --red-dark:#c2161c;
  --green:#1d5e35;
  --white:#ffffff;
  --ink:#1f1f1f;
  --stage:#e9e8e6;
  --mist:#dfe2e8;
  --suit:#2c4a7c;
}
*{margin:0;padding:0;box-sizing:border-box}
html,body{width:1200px;height:3621px;overflow:hidden;background:var(--stage)}
body{position:relative;font-family:"Poppins",sans-serif}
.flyer{position:absolute;left:100px;top:1103px;width:1000px;height:1414px;background:linear-gradient(180deg,#fff 0%,#fff 50%,var(--mist) 75%,#eef0f3 100%);overflow:hidden;box-shadow:0 20px 50px rgba(0,0,0,.18)}
.hero-band{position:absolute;left:79px;top:0;width:432px;height:1278px;background:linear-gradient(180deg,var(--red) 0%,#d71920 60%,var(--red-dark) 100%)}
.hero-band::before,.hero-band::after{content:"";position:absolute;top:0;bottom:0;border-left:2px dashed rgba(255,255,255,.55)}
.hero-band::before{left:14px}
.hero-band::after{right:14px}
.scene-photo{position:absolute;left:0;top:0;width:1000px;height:1414px}
.headline{position:absolute;left:79px;top:0;width:432px;height:500px;color:var(--white);font-family:"Montserrat",sans-serif;font-weight:900;text-transform:uppercase}
.headline span{position:absolute;left:0;width:100%;text-align:center;line-height:1;white-space:nowrap}
.headline .same{top:44px;font-size:110px}
.headline .day{top:158px;font-size:143px}
.headline .tax{top:285px;font-size:155px}
.headline .advance{top:435px;font-size:62px}
.amount-pill{position:absolute;left:126px;top:519px;width:336px;height:80px;background:var(--white);border-radius:14px;display:flex;align-items:center;box-shadow:0 4px 10px rgba(0,0,0,.2)}
.amount-pill .upto{width:76px;height:80px;border-radius:14px 40px 40px 14px;background:var(--green);color:var(--white);font-family:"Montserrat",sans-serif;font-weight:800;font-size:24px;line-height:.95;display:flex;flex-direction:column;align-items:center;justify-content:center}
.amount-pill .value{flex:1;text-align:center;color:var(--red);font-family:"Montserrat",sans-serif;font-weight:900;font-size:60px;line-height:1}
.brand{position:absolute;left:560px;top:60px;width:392px;text-align:center;color:var(--green);font-weight:600;font-size:38px;line-height:1.15}
.brand small{display:block;font-size:20px;font-weight:500;letter-spacing:5px;text-transform:uppercase;margin-top:4px}
.pitch{position:absolute;left:573px;top:228px;width:410px;color:var(--green);font-size:36px;font-weight:500;line-height:48px}
.pitch strong{display:block;color:var(--red);font-weight:800;font-size:42px;line-height:56px}
.features{position:absolute;left:573px;top:384px;width:341px;list-style:none}
.feature{display:flex;align-items:center;height:137px;gap:40px;font-weight:600;font-size:28px;line-height:34px;color:var(--ink)}
.feature + .feature{border-top:2px dashed #c9ccd2}
.feature:last-child{height:130px}
.feature svg{flex:none;width:86px;height:78px}
.feature span{white-space:nowrap}
.pointer{position:absolute;left:812px;top:776px;width:100px;height:176px}
.footer{position:absolute;left:0;top:1278px;width:1000px;height:136px;background:var(--green);border-top:9px solid var(--red)}
.contact-ribbon{position:absolute;left:381px;top:-26px;width:239px;height:38px;line-height:38px;text-align:center;background:var(--red);color:var(--white);font-weight:800;font-size:23px;clip-path:polygon(0 0,100% 0,95% 50%,100% 100%,0 100%,5% 50%)}
.contact{position:absolute;top:42px;display:flex;align-items:center;gap:20px;color:var(--white);line-height:56px;white-space:nowrap}
.contact svg{width:34px;height:34px;flex:none}
.contact.phone{left:99px;font-weight:800;font-size:44px}
.contact.address{left:626px;font-weight:500;font-size:29px;letter-spacing:2px}
</style>
</head>
<body>
<main class="flyer">
  <div class="hero-band"></div>

  <svg class="scene-photo" viewBox="0 0 1000 1414" role="img" aria-label="Photo of a businessman at a desk using a calculator, with a monitor showing a tax form and a laptop beside him">
    <defs>
      <linearGradient id="photoTone" x1="0" y1="0" x2="1" y2="0">
        <stop offset="0" stop-color="#2c4a7c"/>
        <stop offset=".35" stop-color="#3d5a88"/>
        <stop offset=".55" stop-color="#cfd4dc"/>
        <stop offset="1" stop-color="#eceef2"/>
      </linearGradient>
    </defs>
    <path d="M0 658 H330 V795 H1000 V1278 H0 Z" fill="url(#photoTone)"/>
  </svg>

  <h1 class="headline">
    <span class="same">Same</span>
    <span class="day">Day</span>
    <span class="tax">Tax</span>
    <span class="advance">Advance</span>
  </h1>
  <div class="amount-pill"><span class="upto"><span>UP</span><span>TO</span></span><span class="value">$6,000</span></div>

  <div class="brand">Halden<small>Financial Group</small></div>

  <p class="pitch">File your taxes<br>and apply for an<strong>Easy Advance!</strong></p>

  <ul class="features">
    <li class="feature">
      <svg viewBox="0 0 76 70" fill="none" stroke="#1d5e35" stroke-width="3"><rect x="20" y="6" width="50" height="30" rx="3"/><rect x="26" y="12" width="48" height="30" rx="3" stroke-opacity=".5"/><circle cx="45" cy="21" r="8" stroke="#e31e24"/><text x="45" y="26" text-anchor="middle" font-size="12" font-weight="700" fill="#e31e24" stroke="none">$</text><circle cx="20" cy="48" r="16" fill="#fff"/><path d="M20 38v10l7 5"/></svg>
      <span>Available In<br>24 Hours or Less</span>
    </li>
    <li class="feature">
      <svg viewBox="0 0 76 70" fill="none" stroke="#1d5e35" stroke-width="3"><circle cx="32" cy="32" r="16" stroke="#e31e24"/><text x="32" y="39" text-anchor="middle" font-size="18" font-weight="700" fill="#e31e24" stroke="none">$</text><path d="M32 6v6M10 32h6M14 14l4 4M50 14l-4 4"/><path d="M40 40l20 8-8 3 8 9-4 3-8-9-3 8z" fill="#fff"/></svg>
      <span>Choose Your<br>Loan Amount</span>
    </li>
    <li class="feature">
      <svg viewBox="0 0 76 70" fill="none" stroke="#1d5e35" stroke-width="3"><circle cx="44" cy="35" r="22"/><circle cx="44" cy="35" r="15" fill="#e31e24" stroke="#e31e24"/><text x="44" y="42" text-anchor="middle" font-size="20" font-weight="700" fill="#fff" stroke="none">$</text><path d="M4 25h14M8 35h12M4 45h14"/></svg>
      <span>Quick and Easy</span>
    </li>
  </ul>

  <svg class="pointer" viewBox="0 0 100 176" fill="none"><path d="M80 4 C100 70 80 140 22 158" stroke="#e31e24" stroke-width="6" stroke-linecap="round"/><path d="M6 162 L36 136 L38 172 Z" fill="#e31e24"/></svg>

  <footer class="footer">
    <span class="contact-ribbon">Contact Us Today!</span>
    <span class="contact phone"><svg viewBox="0 0 34 34"><rect width="34" height="34" rx="6" fill="#e31e24"/><path d="M11 8c2 0 3 4 3 5s-2 2-2 3 4 6 6 6 1-2 3-2 4 1 4 3-2 4-4 4C14 27 7 20 7 12c0-2 2-4 4-4z" fill="#fff"/></svg>Phone Number</span>
    <span class="contact address"><svg viewBox="0 0 34 34"><rect width="34" height="34" rx="6" fill="#e31e24"/><path d="M17 6a8 8 0 0 1 8 8c0 6-8 14-8 14S9 20 9 14a8 8 0 0 1 8-8z" fill="#fff"/><circle cx="17" cy="14" r="3" fill="#e31e24"/></svg>Address line 1</span>
  </footer>
</main>
</body>
</html>
```